Business card design

Hi,
I need to have a business card design based on the current logo.
If competitive I not put it out to everyone.

It can be single of double sided

Target Market(s)

Food businesses

Industry/Entity Type

Food Manufacturing

Contact Information for Business Card

Details will on card will be as follows Name = Marcus Bell Email = Marcus@PanHearth.com.au Phone = 0418563207 Address = 57 Larkin Street , Fortitude Valley QLD 4006 Australia

Font styles to use
Other font styles liked:
• based on two fonts - Adelle & Museo

Requirements
Must have
• Based on the on switch concept

```html
<!DOCTYPE html>
<html lang="en">
<head>
<meta charset="utf-8">
<title>PanHearth business card</title>
<link rel="stylesheet" href="https://fonts.googleapis.com/css2?family=Arimo:wght@400;700&family=Roboto+Slab:wght@500&display=swap">
<style>
  :root {
    --stage: #2a2a2a;
    --stage-edge: #141414;
    --card-dark: #3f292c;
    --card-red: #ee2849;
    --white: #ffffff;
    --shadow: rgba(0, 0, 0, 0.55);
  }
  * { box-sizing: border-box; margin: 0; padding: 0; }
  html, body {
    width: 1200px;
    height: 1015px;
    overflow: hidden;
  }
  body {
    background: radial-gradient(ellipse at 50% 45%, #4a4a4a 0%, var(--stage) 55%, var(--stage-edge) 100%);
    font-family: "Arimo", Arial, sans-serif;
    position: relative;
  }
  .card {
    position: absolute;
    width: 700px;
    height: 400px;
    box-shadow: 0 18px 40px var(--shadow);
  }
  .card-back {
    left: 110px;
    top: 90px;
    background: var(--card-dark);
    display: flex;
    align-items: center;
    justify-content: center;
  }
  .brand {
    display: flex;
    align-items: center;
    gap: 22px;
  }
  .brand-dot {
    width: 46px;
    height: 46px;
    border-radius: 50%;
    background: var(--card-red);
  }
  .brand-text {
    display: flex;
    flex-direction: column;
    align-items: flex-end;
  }
  .brand-name {
    font-family: "Arimo", Arial, sans-serif;
    font-weight: 700;
    font-size: 64px;
    letter-spacing: 1px;
    color: var(--white);
    line-height: 1;
  }
  .brand-tagline {
    font-family: "Roboto Slab", Georgia, serif;
    font-weight: 500;
    font-size: 17px;
    color: var(--white);
    margin-top: 6px;
    letter-spacing: 0.5px;
  }
  .card-front {
    left: 390px;
    top: 525px;
    background: var(--card-red);
    color: var(--white);
    padding: 58px 0 0 62px;
  }
  .person-name {
    font-weight: 700;
    font-size: 30px;
    letter-spacing: 1.5px;
    text-transform: uppercase;
  }
  .address {
    margin-top: 36px;
    margin-left: 44px;
    font-size: 19px;
    line-height: 1.25;
  }
  .contact-list {
    list-style: none;
    margin-top: 52px;
    margin-left: 88px;
    font-size: 20px;
    line-height: 1.3;
  }
  .contact-list li {
    display: flex;
    align-items: center;
    gap: 9px;
  }
  .contact-icon {
    width: 18px;
    height: 18px;
    flex: none;
  }
</style>
</head>
<body>
  <section class="card card-back" aria-label="Card back">
    <div class="brand">
      <span class="brand-dot" aria-hidden="true"></span>
      <div class="brand-text">
        <span class="brand-name">PANHEARTH</span>
        <span class="brand-tagline">Fresh Kitchen Help On Call</span>
      </div>
    </div>
  </section>

  <section class="card card-front" aria-label="Card front">
    <h1 class="person-name">Marcus Bell</h1>
    <p class="address">
      57 Larkin Street<br>
      Marrowdale Heights<br>
      QLD 4129 Australia
    </p>
    <ul class="contact-list">
      <li>
        <svg class="contact-icon" viewBox="0 0 24 24" aria-hidden="true"><path fill="#fff" d="M6.6 10.8a15 15 0 0 0 6.6 6.6l2.2-2.2a1 1 0 0 1 1-.25 11.4 11.4 0 0 0 3.6.57 1 1 0 0 1 1 1V20a1 1 0 0 1-1 1A17 17 0 0 1 3 4a1 1 0 0 1 1-1h3.5a1 1 0 0 1 1 1c0 1.250.2 2.450.57 3.57a1 1 0 0 1-.25 1z"/></svg>
        0418563207
      </li>
      <li>
        <svg class="contact-icon" viewBox="0 0 24 24" aria-hidden="true"><path fill="#fff" d="M2 5h20v14H2z"/><path fill="none" stroke="#ee2849" stroke-width="1.8" d="M2.5 5.5 12 13l9.5-7.5"/></svg>
        Marcus@PanHearth.com.au
      </li>
      <li>
        <svg class="contact-icon" viewBox="0 0 24 24" aria-hidden="true"><g fill="none" stroke="#fff" stroke-width="1.8"><circle cx="12" cy="12" r="9.5"/><ellipse cx="12" cy="12" rx="4" ry="9.5"/><path d="M2.5 12h19M4 7h16M4 17h16"/></g></svg>
        www.PanHearth.com.au
      </li>
    </ul>
  </section>
</body>
</html>
```